We need a web page design for a new company called "Brambel". We provide an innovative music sharing mobile application that allows music listeners to share their music without paying for a monthly subscription. We would like to incorporate the attached logo and color scheme. The final design should communicate music gifting and sharing.

Industry/Entity Type

It Company

```html
<!DOCTYPE html>
<html lang="en">
<head>
<meta charset="utf-8">
<title>Brambel – own the music</title>
<link href="https://fonts.googleapis.com/css2?family=Oswald:wght@300;400;500&display=swap" rel="stylesheet">
<style>
:root{
  --green:#62ac1c;
  --green-dark:#4a8c0c;
  --green-light:#7cc531;
  --yellow:#ffc21a;
  --orange:#f7a600;
  --ink:#222;
  --text:#333;
  --muted:#777;
  --panel:#fff;
  --page:#f1f1f1;
  --dark:#2a2a2a;
  --darker:#1d1d1d;
  --chip:#e9e9e9;
}
*{box-sizing:border-box;margin:0;padding:0}
html,body{width:953px;height:1200px;overflow:hidden}
body{position:relative;background:var(--page);font-family:Arial,Helvetica,sans-serif;color:var(--text)}
.abs{position:absolute}
.osw{font-family:'Oswald',sans-serif}

/* header */
.site-header{position:absolute;left:0;top:0;width:953px;height:74px;background:linear-gradient(#6bb525,#55a013);border-bottom:3px solid #8fd23f}
.brand{position:absolute;left:156px;top:16px;display:flex;align-items:center;gap:7px;color:#fff}
.brand-dot{width:26px;height:26px;border-radius:50%;background:#fff}
.brand-name{font-family:'Oswald',sans-serif;font-weight:400;font-size:26px;line-height:1}
.brand-tag{position:absolute;left:193px;top:45px;font-size:8px;letter-spacing:2px;color:#bfe59a}
.util{position:absolute;right:156px;top:9px;font-family:'Oswald',sans-serif;font-size:8px;color:#fff;word-spacing:2px}
.util .on{border-bottom:1px solid var(--yellow)}
.nav{position:absolute;left:367px;top:31px;display:flex;gap:0;font-family:'Oswald',sans-serif;font-size:10.5px;color:#fff}
.nav span{margin-right:25px}
.nav .active{color:var(--yellow);border-bottom:2px solid var(--yellow);padding-bottom:3px}
.nav .store{display:flex;align-items:center;gap:4px;margin-right:0}
.nav .store i{width:11px;height:11px;border-radius:50%;background:#fff;display:inline-block}

/* hero */
.hero{position:absolute;left:0;top:77px;width:953px;height:416px;background:linear-gradient(#8fb6d6 0%,#c6dbea 45%,#cfd9c6 68%,#7ea04a 82%,#5e8a2a 100%)}
.hero-title{position:absolute;left:155px;top:170px;font-family:'Oswald',sans-serif;font-weight:400;font-size:40px;color:#fff;letter-spacing:.5px}
.hero-title b{color:#5fae10;font-weight:400}
.hero-sub{position:absolute;left:160px;top:216px;font-size:21px;color:#222}
.cta{position:absolute;left:156px;top:258px;width:143px;height:34px;border-radius:8px;background:linear-gradient(#ffd21c,#f49a00);color:#fff;font-family:'Oswald',sans-serif;font-size:15px;line-height:34px;text-align:center;box-shadow:0 2px 3px rgba(0,0,0,.2)}

/* panel */
.panel{position:absolute;left:143px;top:373px;width:666px;height:750px;background:var(--panel)}
.card{position:absolute;top:383px;width:204px;height:129px;border:1px solid #ccc}
.photo{position:absolute;inset:0}
.label{position:absolute;font-family:'Oswald',sans-serif;font-size:18px;padding:0 5px;height:27px;line-height:27px}
.countdown{position:absolute;left:0;right:0;bottom:0;height:70px;background:rgba(20,20,20,.85)}
.countdown .event{position:absolute;left:0;right:0;top:4px;text-align:center;font-family:'Oswald',sans-serif;color:var(--yellow);font-size:12.5px}
.unit{position:absolute;top:22px;width:44px;text-align:center;color:#fff}
.unit b{display:block;font-family:'Oswald',sans-serif;font-weight:400;font-size:28px;line-height:30px}
.unit small{font-size:6px;font-family:'Oswald',sans-serif}
.tweet{background:#1c1c1c;color:#ddd;padding:13px 14px}
.tweet h4{font-family:'Oswald',sans-serif;font-weight:400;font-size:12px;color:#fff}
.tweet h4 small{font-family:Arial,sans-serif;font-size:7px;color:#888}
.tweet p{font-size:9.5px;line-height:15px;margin-top:5px}
.tweet .follow{position:absolute;left:14px;bottom:14px;font-size:7px;color:#777;display:flex;align-items:center;gap:6px}
.tweet .follow i{width:10px;height:10px;border-radius:50%;background:#4aa3df}

.bar-head{position:absolute;top:525px;height:34px;line-height:34px;padding-left:11px;font-family:'Oswald',sans-serif;font-size:18px;color:#fff}

.news{position:absolute;left:169px;width:397px}
.date{position:absolute;left:0;top:0;width:56px;height:40px;background:var(--dark);color:#fff;text-align:center;box-shadow:2px 2px 0 #bbb}
.date.green{background:var(--green)}
.date small{display:block;font-family:'Oswald',sans-serif;font-size:7px;padding-top:4px}
.date b{display:block;font-family:'Oswald',sans-serif;font-weight:400;font-size:17px;line-height:20px}
.news h3{position:absolute;left:69px;top:0;font-family:'Oswald',sans-serif;font-weight:400;font-size:12px;color:var(--ink);white-space:nowrap}
.news p{position:absolute;left:69px;top:19px;width:328px;font-size:7.4px;line-height:12.2px;color:#777}
.news p em{font-style:normal;color:#999}
.rule{position:absolute;left:169px;width:397px;height:1px;background:#e3e3e3}
.btn-ghost{position:absolute;border:1px solid #bbb;background:linear-gradient(#fff,#eee);font-family:'Oswald',sans-serif;color:#444;text-align:center;box-shadow:0 1px 1px rgba(0,0,0,.15)}

/* player */
.track{position:absolute;left:605px;top:569px;font-family:'Oswald',sans-serif;font-size:11px;color:#333}
.by{position:absolute;left:605px;top:584px;font-size:8px;color:#444}
.slider{position:absolute;left:617px;top:601px;width:150px;height:4px;background:#333;border-radius:2px}
.controls{position:absolute;left:605px;top:615px;width:178px;height:35px;background:linear-gradient(#4a4a4a,#2a2a2a);border:1px solid #222}
.controls .prog{position:absolute;left:0;right:0;bottom:0;height:6px;background:#555}
.controls .prog i{position:absolute;left:0;top:0;bottom:0;width:75%;background:#777}
.times{position:absolute;left:605px;top:657px;width:178px;font-size:8.5px;color:#333;display:flex;justify-content:space-between}
.playlist div{position:absolute;left:605px;width:177px;height:22px;background:var(--chip);font-size:7.5px;color:#444;line-height:22px;padding-left:7px}
.buy-bar{position:absolute;left:592px;top:810px;width:204px;height:33px;background:var(--green);color:#fff;font-family:'Oswald',sans-serif;font-size:12px;line-height:33px;padding-left:13px}
.buy-bar .dots{position:absolute;right:9px;top:10px;display:flex;gap:9px}
.buy-bar .dots i{width:13px;height:13px;border-radius:50%;background:#fff;opacity:.9}

/* store */
.store-title{position:absolute;left:168px;top:866px;font-family:'Oswald',sans-serif;font-weight:300;font-size:18px;color:#222}
.album{position:absolute;top:899px;width:143px}
.album .cover{height:136px;border:1px solid #ccc}
.album h5{margin-top:13px;font-family:'Oswald',sans-serif;font-weight:400;font-size:12px;color:#222;white-space:nowrap}
.album h5.hl{color:var(--green)}
.album .fmt{font-size:7.6px;color:#888;margin-top:5px}
.album .buy{margin-top:8px;display:flex;align-items:center;gap:6px;font-family:'Oswald',sans-serif;font-size:8.5px;color:#888}
.album .buy i{width:10px;height:10px;border-radius:50%;background:#999}
.album .buy .sep{width:1px;height:9px;background:#bbb;margin:0 3px}
.tip{position:absolute;left:243px;top:1053px;height:20px;padding:0 8px;background:var(--green);color:#fff;font-family:'Oswald',sans-serif;font-size:10px;line-height:20px}
.tip:after{content:"";position:absolute;left:50%;bottom:-4px;margin-left:-4px;border:4px solid transparent;border-bottom:0;border-top-color:var(--green)}

/* footer */
.foot{position:absolute;left:143px;top:1123px;width:666px;height:47px;background:var(--dark)}
.foot-brand{position:absolute;left:150px;top:1136px;display:flex;align-items:center;gap:5px;color:var(--green-light)}
.foot-brand i{width:16px;height:16px;border-radius:50%;background:var(--green-light)}
.foot-brand span{font-family:'Oswald',sans-serif;font-size:16px}
.foot-div{position:absolute;top:1123px;width:1px;height:47px;background:#3c3c3c}
.foot-nav{position:absolute;left:238px;top:1141px;font-family:'Oswald',sans-serif;font-size:8.5px;color:#fff;display:flex;gap:7px}
.foot-nav .sl{color:#666}
.foot-nav .on{color:var(--green-light)}
.news-l{position:absolute;left:590px;top:1139px;font-family:'Oswald',sans-serif;font-size:11px;color:#fff}
.email{position:absolute;left:654px;top:1136px;width:108px;height:21px;background:#1c1c1c;font-family:'Oswald',sans-serif;font-size:8px;color:#999;line-height:21px;padding-left:6px}
.submit{position:absolute;left:762px;top:1137px;width:33px;height:19px;background:var(--yellow);font-family:'Oswald',sans-serif;font-size:8px;color:#222;text-align:center;line-height:19px}
.sub-foot{position:absolute;left:143px;top:1170px;width:666px;height:30px;background:var(--darker)}
.copy{position:absolute;left:153px;top:1181px;font-size:7.5px;color:#aaa}
.copy u{color:#ccc}
.follow-us{position:absolute;left:601px;top:1178px;display:flex;align-items:center;gap:7px;font-family:'Oswald',sans-serif;font-size:9.5px;color:#fff}
.follow-us i{width:10px;height:10px;border-radius:50%;background:#555}
.to-top{position:absolute;left:787px;top:1170px;width:22px;height:30px;background:#2a2a2a;color:#777;font-family:'Oswald',sans-serif;font-size:6px;text-align:center;padding-top:15px}
</style>
</head>
<body>

<header class="site-header">
  <div class="brand"><span class="brand-dot"></span><span class="brand-name">Brambel</span></div>
  <div class="brand-tag">own the music</div>
  <div class="util"><span class="on">LOG IN</span> | SIGNUP | SEARCH</div>
  <nav class="nav">
    <span>HOME</span><span>NEWS</span><span class="active">TOUR DATES</span><span>AUDIO</span><span>VIDEOS</span><span>SHARE</span><span>CONTACT</span>
    <span class="store"><i></i>ONLINE STORE</span>
  </nav>
</header>

<section class="hero" role="img" aria-label="Photo of a young woman wearing headphones in a sunny meadow with a city skyline behind"></section>
<h1 class="hero-title">WELCOME TO <b>BRAMBEL</b></h1>
<p class="hero-sub">Lorem ipsum dolor sit amet, consectetuer</p>
<div class="cta">SHARE NOW</div>

<main class="panel"></main>

<!-- feature cards -->
<article class="card" style="left:157px">
  <div class="photo" role="img" aria-label="Photo of a singer with a guitar on stage" style="background:linear-gradient(135deg,#b8b8b8,#6a6a6a)"></div>
  <div class="label" style="left:6px;top:8px;background:#111;color:#fff">NEXT EVENT</div>
  <div class="countdown">
    <div class="event">SKYFEST - RIVERSIDE FIELD</div>
    <div class="unit" style="left:14px"><b>03</b><small>DAYS</small></div>
    <div class="unit" style="left:58px"><b>23</b><small>HOURS</small></div>
    <div class="unit" style="left:102px"><b>59</b><small>MINUTES</small></div>
    <div class="unit" style="left:146px"><b>26</b><small>SECS</small></div>
  </div>
</article>

<article class="card" style="left:374px">
  <div class="photo" role="img" aria-label="Photo of a couple dancing under colourful party lights" style="background:linear-gradient(120deg,#3b2a8a,#c0306a 45%,#e8a040 75%,#3a5cc0)"></div>
  <div class="label" style="left:8px;top:10px;background:var(--green);color:#fff;font-size:19px">JUST ARRIVED</div>
</article>

<article class="card tweet" style="left:592px">
  <h4>DAN HARLOW <small>4 hours Ago</small></h4>
  <p>If you enjoyed Quiet Harbor last night on Reel9, you may like this 10 minute interview special with the stars/director. http://brmb.li/x7k2q</p>
  <div class="follow"><i></i>Follow Us Chirper</div>
</article>

<!-- latest news -->
<div class="bar-head" style="left:157px;width:421px;background:#1f1f1f">LATEST FROM BRAMBEL</div>

<div class="news" style="top:573px">
  <div class="date green"><small>WEDNESDAY</small><b>29JUN</b></div>
  <h3>JAMIE REACHES NUMBER 1 IN THE SPANISH TUNESHOP CHART!</h3>
  <p>Lorem ipsum dolor sit amet, consectetur adipiscing elit. In tellus orci, semper et ornare dictum, varius ut tellus. In consecteturconsectetur adipiscing elit. In tellus orci, semper et ornare dictum, varius ut tellus. ... <em>Read More</em></p>
</div>
<div class="rule" style="top:639px"></div>

<div class="news" style="top:653px">
  <div class="date"><small>SUNDAY</small><b>03JUL</b></div>
  <h3>MIAMI 2012 - DATE AND LINE-UP UPDATE!</h3>
  <p>Lorem ipsum dolor sit amet, consectetur adipiscing elit. In tellus orci, semper et ornare dictum, varius ut tellus. In consecteturconsectetur adipiscing elit. In tellus orci, semper et ornare dictum, varius ut tellus. ... <em>Read More</em></p>
</div>
<div class="rule" style="top:717px"></div>

<div class="news" style="top:731px">
  <div class="date"><small>FRIDAY</small><b>01AUG</b></div>
  <h3>EXCLUSIVE VIDEO: ON THE FLOOR IN SOUTH AMERICA</h3>
  <p>Lorem ipsum dolor sit amet, consectetur adipiscing elit. In tellus orci, semper et ornare dictum, varius ut tellus. In consecteturconsectetur adipiscing elit. In tellus orci, semper et ornare dictum, varius ut tellus. ... <em>Read More</em></p>
</div>
<div class="rule" style="top:800px"></div>

<div class="btn-ghost" style="left:171px;top:809px;width:122px;height:24px;line-height:22px;font-size:10px">VIEW ALL NEWS AND EVENT</div>

<!-- now playing -->
<div class="bar-head" style="left:592px;width:204px;background:var(--green)">NOW PLAYING</div>
<div class="track">GROW US WITH ME</div>
<div class="by">by: Leo Marsh</div>
<svg class="abs" style="left:605px;top:597px" width="180" height="12" viewBox="0 0 180 12">
  <path d="M1 4h2l3-3v10l-3-3H1z" fill="#444"/>
  <path d="M168 4h2l3-3v10l-3-3h-2z" fill="#444"/><path d="M175 3q2 3 0 6M177 1q4 5 0 10" stroke="#444" fill="none"/>
</svg>
<div class="slider"></div>
<div class="controls">
  <svg width="178" height="29" viewBox="0 0 178 29">
    <g stroke="#1e1e1e"><line x1="44.5" y1="0" x2="44.5" y2="29"/><line x1="89.5" y1="0" x2="89.5" y2="29"/><line x1="134.5" y1="0" x2="134.5" y2="29"/></g>
    <path d="M22 9l-8 6 8 6zM30 9l-8 6 8 6z" fill="#111"/>
    <path d="M62 8l12 7-12 7z" fill="#111"/>
    <path d="M105 9l8 6-8 6zM113 9l8 6-8 6z" fill="#111"/>
    <rect x="150" y="9" width="12" height="12" rx="2" fill="#111"/>
  </svg>
  <div class="prog"><i></i></div>
</div>
<div class="times"><span>00:00</span><span>04:27</span></div>
<svg class="abs" style="left:665px;top:656px" width="60" height="12" viewBox="0 0 60 12">
  <g stroke="var(--green)" stroke-width="1.6" fill="none">
    <path d="M10 6a4 4 0 1 1-2-3.5"/><path d="M7 1l2 2-2 2"/>
    <path d="M24 3h3l6 6h3M24 9h3l6-6h3"/>
    <path d="M47 3h9M47 6h9M47 9h9"/>
  </g>
</svg>
<div class="playlist">
  <div style="top:686px">Esse molestie consequat vel illum</div>
  <div style="top:715px">Molestie consequat vel illum</div>
  <div style="top:744px">Eolestie consequat user one</div>
  <div style="top:773px">Eolestie consequat user one</div>
</div>
<div class="buy-bar">BUY NOW<span class="dots"><i></i><i></i><i></i><i></i></span></div>

<!-- store -->
<h2 class="store-title">BUY FROM OUR STORE</h2>
<div class="btn-ghost" style="left:713px;top:869px;width:69px;height:17px;line-height:15px;font-size:7.5px">VIEW ALL ALBUMS</div>

<div class="album" style="left:170px">
  <div class="cover" role="img" aria-label="Album cover of two women at a party with a red side banner" style="background:linear-gradient(120deg,#d79a6e,#a24434 60%,#6b1a1a)"></div>
  <h5>THE FLOOR IN SOUTH AMERICA</h5>
  <div class="fmt">MP3 CD Library Binding</div>
  <div class="buy">BUY NOW<span class="sep"></span><i></i><i style="background:#333"></i><i></i><i></i></div>
</div>
<div class="album" style="left:326px">
  <div class="cover" role="img" aria-label="Album cover of a smiling man beside a turquoise title card" style="background:linear-gradient(120deg,#8d8d8d,#d8d8d8 50%,#5ab4c8)"></div>
  <h5 class="hl">DATE AND LINE-UP</h5>
  <div class="fmt">MP3 CD Library Binding</div>
  <div class="buy">BUY NOW<span class="sep"></span><i></i><i></i><i></i></div>
</div>
<div class="album" style="left:483px">
  <div class="cover" role="img" aria-label="Album cover of two friends in sunglasses over hand-drawn lettering" style="background:linear-gradient(160deg,#e8d08a,#d6c3a8 50%,#9a9a9a)"></div>
  <h5>SPANISH TUNESHOP</h5>
  <div class="fmt">MP3 CD Library Binding</div>
  <div class="buy">BUY NOW<span class="sep"></span><i></i><i></i></div>
</div>
<div class="album" style="left:639px;top:897px">
  <div class="cover" role="img" aria-label="Album cover of a rock guitarist with bold black title lettering" style="height:144px;background:linear-gradient(120deg,#f0f0f0,#cfcfcf 60%,#555)"></div>
  <h5 style="margin-top:7px">ORBIT FM</h5>
  <div class="fmt">MP3 CD Library Binding</div>
  <div class="buy">BUY NOW<span class="sep"></span><i></i><i></i><i></i></div>
</div>
<div class="tip">TUNESHOP</div>

<!-- footer -->
<footer>
  <div class="foot"></div>
  <div class="foot-brand"><i></i><span>Brambel</span></div>
  <div class="foot-div" style="left:224px"></div>
  <nav class="foot-nav">
    <span>HOME</span><span class="sl">/</span><span>NEWS</span><span class="sl">/</span><span class="on">TOUR DATES</span><span class="sl">/</span><span>AUDIO</span><span class="sl">/</span><span>VIDEOS</span><span class="sl">/</span><span>GALLERY</span><span class="sl">/</span><span>CONTACT</span>
  </nav>
  <div class="foot-div" style="left:578px"></div>
  <div class="news-l">NEWSLETTER</div>
  <div class="email">ENTER EMAIL ADDRESS</div>
  <div class="submit">SUBMIT</div>
  <div class="sub-foot"></div>
  <div class="copy">Copyright <u>Brambel</u> 2014</div>
  <div class="follow-us">FOLLOW US<i></i><i></i><i></i><i></i><i></i><i></i><i></i></div>
  <div class="to-top">TOP</div>
</footer>

</body>
</html>
```